High value cover design for an A4 ideation pad.

The product is NOT A BOOK.

It's an A4 ideation pad for professionals, designers and creators who handwrite their ideas. Visualise creators like Milo Varnet, Owen Plaskit and Gregor Lunwick in your mind's eye.

I'm looking for a cover design for the ideation pad. Both front and back.

It should look, feel and convey the following.

--> A handcrafted product experience

--> High value & Elegance

--> Inspiration

Mandatory --> See Uploaded Files --> Files 1, 5 & 6

Target Market(s)

- Designers

-Creative Professionals

- Entrepreneurs

who handwrite their ideas. Visualise creators like Milo Varnet, Owen Plaskit and Gregor Lunwick in your mind's eye.

Industry/Entity Type

Stationary

Font styles to use
Script
Other font styles liked:
• Calligraphy

Colors
fbed22

Requirements
Must have
• Title text - Quiet Kettle Notes

-Text in gold on brown leather background to convey high value for the front cover.

--> High value & Elegance

--> Inspiration

--> Should compel the customers to pick up and own the idea pad
Nice to have
• That's my take but other ideas are welcome
Should not have
• Must not convey

- low value

```html
<!DOCTYPE html>
<html lang="en">
<head>
<meta charset="utf-8">
<title>Quiet Kettle Notes — Pad Covers</title>
<link rel="stylesheet" href="https://fonts.googleapis.com/css2?family=Marcellus&family=Gotu&family=Montserrat:wght@300;400;700&display=swap">
<style>
  :root {
    --bg: #2e3235;
    --cover: #08080c;
    --cover-edge: #0d0d12;
    --gold: #e0a82a;
    --gold-light: #fbed22;
    --gold-deep: #b47a12;
    --ink-light: #e9e9ec;
    --ink-dark: #1b1406;
  }
  * { margin: 0; padding: 0; box-sizing: border-box; }
  html, body { width: 1200px; height: 900px; overflow: hidden; }
  body { background: var(--bg); position: relative; font-family: "Gotu", sans-serif; }

  .cover {
    position: absolute;
    top: 189px;
    width: 377px;
    height: 526px;
    background: linear-gradient(160deg, var(--cover-edge), var(--cover) 60%);
    border-radius: 4px;
    box-shadow: 0 10px 24px rgba(0,0,0,.55);
  }
  .cover--back { left: 150px; }
  .cover--front { left: 556px; }

  .pattern-gold {
    position: absolute;
    left: 0; top: 77px;
    width: 133px; height: 390px;
    background: linear-gradient(180deg, #6e4d10, #8a6216 50%, #5e420d);
    opacity: .85;
  }

  .location { position: absolute; left: 186px; top: 362px; color: var(--ink-light); }
  .location__title {
    font-family: "Montserrat", sans-serif;
    font-weight: 700;
    font-size: 12px;
    letter-spacing: .2px;
    color: var(--gold);
    margin-bottom: 14px;
  }
  .contact { list-style: none; font-size: 9.5px; line-height: 12.5px; }
  .contact li { display: flex; align-items: flex-start; gap: 6px; margin-bottom: 4px; }
  .contact svg { flex: 0 0 11px; width: 11px; height: 11px; margin-top: 0.5px; }

  .pattern-dark {
    position: absolute;
    left: 122px; top: 20px;
    width: 134px; height: 462px;
    background: linear-gradient(180deg, #121218, #17171e 50%, #111116);
  }
  .title-frame {
    position: absolute;
    left: 69px; top: 182px;
    width: 236px; height: 136px;
    border: 1px solid var(--gold-deep);
    background: var(--cover);
    text-align: center;
  }
  .gold-text {
    background: linear-gradient(180deg, var(--gold-light), var(--gold) 55%, var(--gold-deep));
    -webkit-background-clip: text;
    background-clip: text;
    color: transparent;
    font-family: "Marcellus", serif;
  }
  .title-frame__kicker { display: block; font-size: 19px; margin-top: 30px; line-height: 1; }
  .title-frame__main { display: block; font-size: 58px; line-height: 1; margin-top: 2px; letter-spacing: -1px; }

  .web-tag {
    position: absolute;
    left: 122px; top: 489px;
    width: 134px; height: 37px;
    background: linear-gradient(180deg, #f1bf3a, #d79e1f);
    color: var(--ink-dark);
    font-family: "Montserrat", sans-serif;
    font-weight: 300;
    font-size: 8.5px;
    display: flex; align-items: center; justify-content: center;
  }

  .sticker {
    position: absolute;
    left: 970px; top: 210px;
    width: 180px; height: 180px;
    border-radius: 50%;
    background: var(--cover);
    box-shadow: 0 6px 16px rgba(0,0,0,.5);
    text-align: center;
    padding-top: 36px;
  }
  .sticker__kicker { display: block; font-size: 11px; line-height: 1; }
  .sticker__main { display: block; font-size: 31px; line-height: 1; letter-spacing: -.5px; }
  .sticker__body {
    width: 150px;
    margin: 8px auto 0;
    font-family: "Montserrat", sans-serif;
    font-size: 4.6px;
    line-height: 5.9px;
    color: var(--ink-light);
  }
</style>
</head>
<body>

<section class="cover cover--back" aria-label="Back cover">
  <div class="pattern-gold" role="img" aria-label="Gold geometric cube line pattern"></div>
  <div class="location">
    <h2 class="location__title">OUR LOCATION</h2>
    <ul class="contact">
      <li>
        <svg viewBox="0 0 12 12"><circle cx="6" cy="6" r="6" fill="#e0a82a"/><path d="M6 2.6a2.2 2.2 0 0 0-2.2 2.2C3.8 6.6 6 9.4 6 9.4s2.2-2.8 2.2-4.6A2.2 2.2 0 0 0 6 2.6z" fill="#08080c"/><circle cx="6" cy="4.8" r=".8" fill="#e0a82a"/></svg>
        <span>41 Marlow Lane<br>Fernhill, Castwick</span>
      </li>
      <li>
        <svg viewBox="0 0 12 12"><circle cx="6" cy="6" r="6" fill="#e0a82a"/><path d="M4 3l1.2 1.4-.6.9c.4.9 1.1 1.6 2 2l.9-.6L9 7.9 8.2 9C5.7 8.8 3.2 6.3 3 3.8z" fill="#08080c"/></svg>
        <span>0 400 218 733 62</span>
      </li>
      <li>
        <svg viewBox="0 0 12 12"><circle cx="6" cy="6" r="6" fill="#e0a82a"/><rect x="3" y="4" width="6" height="4.2" fill="#08080c"/><path d="M3 4l3 2.3L9 4" stroke="#e0a82a" stroke-width=".6" fill="none"/></svg>
        <span>hello@quietkettle.com</span>
      </li>
      <li>
        <svg viewBox="0 0 12 12"><circle cx="6" cy="6" r="6" fill="#e0a82a"/><circle cx="6" cy="6" r="3" fill="none" stroke="#08080c" stroke-width=".7"/><path d="M3 6h6M6 3c-1.2 1.6-1.2 4.4 0 6M6 3c1.2 1.6 1.2 4.4 0 6" stroke="#08080c" stroke-width=".6" fill="none"/></svg>
        <span>www.quietkettle.com</span>
      </li>
    </ul>
  </div>
</section>

<section class="cover cover--front" aria-label="Front cover">
  <div class="pattern-dark" role="img" aria-label="Faint dark geometric cube line pattern"></div>
  <div class="title-frame">
    <h1>
      <span class="title-frame__kicker gold-text">QUIET KETTLE</span>
      <span class="title-frame__main gold-text">NOTES</span>
    </h1>
  </div>
  <div class="web-tag">www.quietkettle.com</div>
</section>

<aside class="sticker" aria-label="Round sticker">
  <span class="sticker__kicker gold-text">QUIET KETTLE</span>
  <span class="sticker__main gold-text">NOTES</span>
  <p class="sticker__body">Quiet pages for loud ideas. Every sheet is made to catch the sketch, the list and the sudden plan before it slips away. Keep it near, write freely and return to the thoughts worth building. Good ideas start small, in ink, on paper, with a steady hand and a clear mind ready for the next page.</p>
</aside>

</body>
</html>
```